Tall Fern Roofing Business Card

Need a business card with the logo that was designed here

Contact Information for Business Card

Name, Title, Phone, Email, Website, Company name

```html
<!DOCTYPE html>
<html lang="en">
<head>
<meta charset="utf-8">
<title>Tall Fern Roofing – Business Card</title>
<link href="https://fonts.googleapis.com/css2?family=Montserrat:wght@500;600;700&display=swap" rel="stylesheet">
<style>
  :root {
    --page-bg: #d9d2c7;
    --card-frost-top: #f3f1ec;
    --card-frost-bottom: #dcd6cc;
    --band-blue: #3470c4;
    --panel-blue-top: #2f64ad;
    --panel-blue-bottom: #2a5290;
    --gap-light: #e8e2d8;
    --brand-blue: #2f6fc4;
    --name-tan: #e2d2b8;
    --text-cream: #ece3d4;
  }
  * { box-sizing: border-box; margin: 0; padding: 0; }
  html, body {
    width: 1200px; height: 897px; overflow: hidden;
    background: var(--page-bg);
    font-family: "Montserrat", sans-serif;
  }
  .business-card {
    position: absolute; left: 80px; top: 163px;
    width: 1040px; height: 570px;
    border-radius: 22px; overflow: hidden;
    background: linear-gradient(180deg, var(--card-frost-top), var(--card-frost-bottom));
    box-shadow: 0 18px 40px rgba(60, 45, 30, 0.25);
  }
  .brand {
    position: absolute; left: 46px; top: 92px;
    display: flex; align-items: center; gap: 14px;
    color: var(--brand-blue);
    font-weight: 700; font-size: 40px; letter-spacing: 0.5px;
  }
  .brand-square { width: 26px; height: 26px; background: var(--brand-blue); }
  .accent-band {
    position: absolute; left: 0; top: 245px; width: 100%; height: 26px;
    background: var(--band-blue);
  }
  .band-gap {
    position: absolute; left: 0; top: 271px; width: 100%; height: 6px;
    background: var(--gap-light);
  }
  .info-panel {
    position: absolute; left: 0; top: 277px; width: 100%; bottom: 0;
    background: linear-gradient(180deg, var(--panel-blue-top), var(--panel-blue-bottom));
  }
  .person-name {
    position: absolute; left: 46px; top: 54px;
    font-weight: 700; font-size: 33px; letter-spacing: 1.2px;
    color: var(--name-tan);
  }
  .person-title {
    position: absolute; left: 46px; top: 98px;
    font-weight: 500; font-size: 21px; letter-spacing: 0.6px;
    color: var(--text-cream);
  }
  .contact-list {
    position: absolute; left: 46px; top: 148px;
    list-style: none; display: flex; flex-direction: column; gap: 14px;
  }
  .contact-item {
    display: flex; align-items: center; gap: 12px;
    font-weight: 500; font-size: 22px; letter-spacing: 0.6px;
    color: var(--text-cream); height: 27px;
  }
  .contact-icon { width: 18px; height: 18px; flex: none; }
  .address {
    position: absolute; right: 46px; top: 192px;
    text-align: right; font-style: normal;
    font-weight: 500; font-size: 22px; line-height: 34px; letter-spacing: 0.6px;
    color: var(--text-cream);
  }
</style>
</head>
<body>
  <article class="business-card">
    <div class="brand">
      <span class="brand-square"></span>
      <span class="brand-name">Tall Fern Roofing</span>
    </div>

    <div class="accent-band"></div>
    <div class="band-gap"></div>

    <section class="info-panel">
      <h1 class="person-name">DECLAN HARTLEY</h1>
      <p class="person-title">Managing Director</p>

      <ul class="contact-list">
        <li class="contact-item">
          <svg class="contact-icon" viewBox="0 0 24 24" fill="var(--text-cream)" aria-hidden="true">
            <path d="M6.6 10.8a15 15 0 0 0 6.6 6.6l2.2-2.2a1 1 0 0 1 1-.25 11.4 11.4 0 0 0 3.6.57 1 1 0 0 1 1 1V20a1 1 0 0 1-1 1A17 17 0 0 1 3 4a1 1 0 0 1 1-1h3.5a1 1 0 0 1 1 1c0 1.25.2 2.45.57 3.57a1 1 0 0 1-.25 1z"/>
          </svg>
          <span>0491 570 226</span>
        </li>
        <li class="contact-item">
          <svg class="contact-icon" viewBox="0 0 24 24" fill="var(--text-cream)" aria-hidden="true">
            <path d="M3 6h18v12H3z" fill="none" stroke="var(--text-cream)" stroke-width="2"/>
            <path d="M3 6l9 7 9-7" fill="none" stroke="var(--text-cream)" stroke-width="2"/>
          </svg>
          <span>info@tallfernroofing.com</span>
        </li>
        <li class="contact-item">
          <svg class="contact-icon" viewBox="0 0 24 24" fill="none" stroke="var(--text-cream)" stroke-width="2" aria-hidden="true">
            <circle cx="12" cy="12" r="9"/>
            <path d="M3 12h18M12 3c3 3.5 3 14.5 0 18M12 3c-3 3.5-3 14.5 0 18"/>
          </svg>
          <span>www.tallfernroofing.com</span>
        </li>
      </ul>

      <address class="address">
        1480 W Marlow Street<br>
        Harwick County Name 4172
      </address>
    </section>
  </article>
</body>
</html>
```